OBK Farcoast Logistics Limited

We need the buissnes card to be very exclusive. As we are all young in our company. We need this to be the gate to make our clients feel deep interest for us.

We are focused in as International Trade advisors, and our products go from Oil Tanker Ships to Rubber balls for dogs.

Our Slogan is Bringing Distance Closer.
And our main marketing will be through Internet.

We were stablished in 2009 In Mexico and we also have offices in Hong Kong.
We have representatives in China and Europe.

Target Market(s)

Is every company or Individual that wants to develop an International Project or product development or Logistic service of Goods and people.
Some of our current projects are Ship Brokerage, Mine Brokerage, Real State and Product Pormotional development.

Industry/Entity Type

It Company

Requirements
Must have
• Our Logo and slogan, and make the card accoriding to the logo.
Nice to have
• Our Colors

```html
<!DOCTYPE html>
<html lang="en">
<head>
<meta charset="utf-8">
<title>OBK – Business Card</title>
<link rel="stylesheet" href="https://fonts.googleapis.com/css2?family=Open+Sans:wght@400;600;700&display=swap">
<style>
  :root {
    --stage: #eceff2;
    --card: #ffffff;
    --band: #1b7cb6;
    --brand: #1b7cb6;
    --accent: #8cc63f;
    --ink: #3b3b3b;
    --on-band: #ffffff;
    --shadow: rgba(0, 0, 0, 0.18);
  }
  * { box-sizing: border-box; margin: 0; padding: 0; }
  html, body {
    width: 1200px; height: 720px; overflow: hidden;
    background: var(--stage);
    font-family: "Open Sans", Arial, sans-serif;
  }
  .stage {
    position: relative; width: 1200px; height: 720px;
    display: flex; align-items: center; justify-content: center; gap: 40px;
  }
  .card {
    position: relative; width: 540px; height: 309px;
    background: var(--card); overflow: hidden;
    box-shadow: 0 6px 18px var(--shadow);
  }

  /* Front card */
  .card-front .brand {
    position: absolute; top: 22px; left: 0; right: 0;
    display: flex; flex-direction: column; align-items: center;
  }
  .brand-mark { display: flex; align-items: center; gap: 8px; }
  .brand-dot { width: 16px; height: 16px; border-radius: 50%; background: var(--accent); }
  .brand-name {
    font-weight: 700; font-size: 36px; letter-spacing: 1px; color: var(--brand); line-height: 1;
  }
  .brand-tagline { margin-top: 6px; font-size: 11px; color: var(--ink); letter-spacing: 0.3px; }

  .info-band {
    position: absolute; left: 0; right: 0; bottom: 0; height: 170px;
    background: var(--band); color: var(--on-band);
    padding: 28px 30px 0;
  }
  .band-circle {
    position: absolute; right: 40px; top: -20px; width: 110px; height: 110px;
    border-radius: 50%; background: rgba(255, 255, 255, 0.12);
  }
  .holder { font-size: 16px; margin-bottom: 8px; }
  .holder-name { font-weight: 700; }
  .contact-list { list-style: none; font-size: 13px; line-height: 1.65; }
  .contact-list li { display: flex; align-items: center; gap: 8px; }
  .contact-list svg { width: 12px; height: 12px; flex: none; fill: var(--on-band); }
  .contact-gap { margin-left: 14px; }

  /* Back card */
  .card-back {
    display: flex; flex-direction: column; align-items: center; justify-content: center;
  }
  .back-circle {
    position: absolute; left: 50%; top: 46%; width: 250px; height: 250px;
    transform: translate(-50%, -50%); border-radius: 50%;
    background: rgba(27, 124, 182, 0.07);
  }
  .back-name {
    position: relative; font-weight: 700; font-size: 92px; letter-spacing: 2px;
    color: var(--brand); line-height: 1; margin-top: -10px;
  }
  .back-tagline { position: relative; font-size: 22px; color: var(--ink); margin-top: 6px; }
  .back-web {
    position: absolute; bottom: 34px; left: 0; right: 0; text-align: center;
    font-size: 15px; letter-spacing: 3px; color: var(--ink); font-weight: 600;
  }
</style>
</head>
<body>
<main class="stage">
  <section class="card card-front" aria-label="Business card front">
    <div class="brand">
      <div class="brand-mark">
        <span class="brand-dot"></span>
        <span class="brand-name">OBK</span>
      </div>
      <p class="brand-tagline">Bringing Distance Closer</p>
    </div>
    <div class="info-band">
      <span class="band-circle"></span>
      <p class="holder"><span class="holder-name">Your Name,</span> Position</p>
      <ul class="contact-list">
        <li>
          <svg viewBox="0 0 12 12"><path d="M2.5 1h2l1 2.6-1.3.9a6.5 6.5 0 0 0 3.3 3.3l.9-1.3 2.6 1v2c0 .8-.7 1.5-1.5 1.5A9 9 0 0 1 1 2.5C1 1.7 1.7 1 2.5 1z"/></svg>
          123-456-7890
          <svg class="contact-gap" viewBox="0 0 12 12"><rect x="3" y="0.5" width="6" height="11" rx="1.2"/></svg>
          123-456-7890
        </li>
        <li>
          <svg viewBox="0 0 12 12"><path d="M1 2.5h10v7H1z"/><path d="M1 2.5l5 4 5-4" fill="none" stroke="#1b7cb6" stroke-width="1"/></svg>
          info@obklinkway.com
        </li>
        <li>
          <svg viewBox="0 0 12 12"><circle cx="6" cy="6" r="5"/><path d="M1 6h10M6 1c2 2.5 2 7.5 0 10M6 1c-2 2.5-2 7.5 0 10" fill="none" stroke="#1b7cb6" stroke-width="0.8"/></svg>
          www.obklinkway.com
        </li>
        <li>
          <svg viewBox="0 0 12 12"><path d="M6 0.5a4 4 0 0 1 4 4c0 3-4 7-4 7s-4-4-4-7a4 4 0 0 1 4-4z"/></svg>
          00, Complex Name, City, State, 00045
        </li>
      </ul>
    </div>
  </section>

  <section class="card card-back" aria-label="Business card back">
    <span class="back-circle"></span>
    <p class="back-name">OBK</p>
    <p class="back-tagline">Bringing Distance Closer</p>
    <p class="back-web">www.obklinkway.com</p>
  </section>
</main>
</body>
</html>
```